Design a book cover
TItle: Where Would Mercy Stand?
Suggested graphic: Jesus holding a gun
Subtitle: A public defender's views on the death penalty
Author Name: Gordon Maskelyne

```html
<!DOCTYPE html>
<html lang="en">
<head>
<meta charset="utf-8">
<title>Where Would Mercy Stand? — Book Cover</title>
<link rel="stylesheet" href="https://fonts.googleapis.com/css2?family=Cinzel:wght@400&family=Libre+Baskerville&display=swap">
<style>
  :root {
    --cover-brown: #683821;
    --title-orange: #f5a53f;
    --author-orange: #f3a645;
    --subtitle-white: #ffffff;
    --art-light: #fbc470;
    --art-mid: #f5a043;
    --art-deep: #e07a2a;
  }
  html, body {
    margin: 0;
    padding: 0;
    overflow: hidden;
    background: var(--cover-brown);
  }
  .cover {
    position: relative;
    width: 800px;
    height: 1200px;
    background: var(--cover-brown);
    overflow: hidden;
  }
  .title {
    position: absolute;
    top: 58px;
    left: 0;
    width: 800px;
    margin: 0;
    font-family: "Cinzel", "Trajan Pro", serif;
    font-weight: 400;
    font-size: 124px;
    line-height: 124px;
    color: var(--title-orange);
    text-align: center;
    text-transform: uppercase;
    letter-spacing: 0;
  }
  .title span { display: block; white-space: nowrap; }
  .title .line-1 { padding-left: 30px; }
  .title .line-4 { padding-left: 30px; }
  .cover-art {
    position: absolute;
    left: 124px;
    top: 573px;
    width: 548px;
    height: 325px;
    border-radius: 48% 48% 10% 10% / 60% 60% 12% 12%;
    background: radial-gradient(ellipse at 50% 40%, var(--art-light) 0%, var(--art-mid) 55%, var(--art-deep) 100%);
  }
  .subtitle {
    position: absolute;
    top: 935px;
    left: 0;
    width: 800px;
    margin: 0;
    font-family: "Libre Baskerville", Georgia, serif;
    font-size: 31px;
    line-height: 42px;
    color: var(--subtitle-white);
    text-align: center;
    letter-spacing: 0.5px;
  }
  .author {
    position: absolute;
    top: 1083px;
    left: 0;
    width: 800px;
    margin: 0;
    font-family: "Cinzel", "Trajan Pro", serif;
    font-weight: 400;
    font-size: 52px;
    line-height: 64px;
    color: var(--author-orange);
    text-align: center;
    text-transform: uppercase;
    letter-spacing: 2px;
    white-space: nowrap;
  }
</style>
</head>
<body>
  <main class="cover">
    <h1 class="title">
      <span class="line-1">Where</span>
      <span class="line-2">Would</span>
      <span class="line-3">Mercy</span>
      <span class="line-4">Stand?</span>
    </h1>
    <div class="cover-art" role="img" aria-label="Cover illustration in warm glowing orange tones"></div>
    <p class="subtitle">A public defender's views on<br>the death penalty</p>
    <p class="author">Gordon Maskelyne</p>
  </main>
</body>
</html>
```